Calm Summit website development

Need a website designed for a coaching business. Very high-end, luxury, professionalism, in the area of STRESS, see brief attached. I have a logo already
Updates

Slow in providing feedback

Target Market(s)

CEOs very successful men and wealthy females, high end luxury market

Industry/Entity Type

coaching

Number of Pages Required

1 page

Requirements
Must have
• Luxury look, professional, serious but warm, appealing to both sexes

```html
<!DOCTYPE html>
<html lang="en">
<head>
<meta charset="UTF-8">
<title>Calm Summit – Lifestyle Coaching</title>
<link href="https://fonts.googleapis.com/css2?family=Oswald:wght@500;600&family=Montserrat:wght@500;600;700&family=Lato:wght@400;700&display=swap" rel="stylesheet">
<style>
:root{
  --blue:#1a6dc4;
  --ink:#1f1e21;
  --text:#2b2b2e;
  --mist:#f2f0f3;
  --frame:#5a5a5e;
  --footer:#1d1c1f;
  --white:#ffffff;
}
*{box-sizing:border-box;margin:0;padding:0}
html,body{width:1200px;height:2993px;overflow:hidden}
body{font-family:'Lato',sans-serif;color:var(--text);background:var(--white);position:relative}
.abs{position:absolute}
.btn{position:absolute;background:var(--blue);color:var(--white);font-family:'Montserrat',sans-serif;font-weight:500;font-size:14px;display:flex;align-items:center;justify-content:center;gap:10px}
.arrow{width:24px;height:10px}

/* hero */
.hero{position:absolute;left:0;top:0;width:1200px;height:653px;background:linear-gradient(180deg,#fbf6e8 0%,#f1e3c2 35%,#d9ba7d 70%,#b98d45 100%)}
.hero-photo{position:absolute;left:0;top:0;width:700px;height:653px;background:radial-gradient(ellipse at 55% 45%,rgba(230,200,150,.6),rgba(0,0,0,0) 60%)}
.brand{position:absolute;display:flex;align-items:center;gap:10px;font-family:'Oswald',sans-serif;font-weight:500;letter-spacing:3px}
.brand-mark{width:18px;height:18px}
.header-brand{left:131px;top:88px;font-size:22px;color:var(--ink)}
.header-brand .brand-mark{background:var(--ink)}
.nav{position:absolute;top:47px;left:0;font-family:'Montserrat',sans-serif;font-weight:500;font-size:13px;color:var(--ink)}
.nav a{position:absolute;color:inherit;text-decoration:none;white-space:nowrap}
.nav a.active{color:var(--blue);font-weight:700;border-bottom:2px solid var(--blue);padding-bottom:5px}
.consult{position:absolute;left:1073px;top:0;width:127px;height:100px;background:var(--blue);color:var(--white);font-family:'Montserrat',sans-serif;font-size:15px;line-height:21px;padding:19px 0 0 25px}
.hero-title{left:710px;top:214px;font-family:'Oswald',sans-serif;font-weight:600;font-size:64px;letter-spacing:7px;color:#111}
.hero-copy{left:710px;top:303px;width:380px;font-size:17px;line-height:25px;color:#222}
.dots{position:absolute;left:570px;top:613px;display:flex;gap:6px}
.dots span{width:8px;height:8px;border-radius:50%;background:var(--white)}
.dots span.on{background:var(--blue)}

/* audience */
.audience{position:absolute;left:0;top:653px;width:1200px;height:827px;background:var(--mist)}
.hex{position:absolute;width:267px;height:321px;clip-path:polygon(50% 0,100% 25%,100% 75%,50% 100%,0 75%,0 25%)}
.hex-photo{position:absolute;inset:0}
.hex-band{position:absolute;left:0;top:235px;width:100%;height:36px;background:rgba(255,255,255,.82);display:flex;align-items:center;justify-content:center;gap:14px;font-family:'Montserrat',sans-serif;font-weight:600;font-size:14px;color:var(--ink)}
.hex-base{position:absolute;left:0;top:271px;width:100%;height:50px;background:#2a2522}
.welcome-photo{left:93px;top:385px;width:436px;height:442px;background:linear-gradient(160deg,#e9e6ea 0%,#d8d3d6 50%,#b9a8a0 100%)}
.eyebrow{left:581px;top:452px;font-family:'Montserrat',sans-serif;font-weight:600;font-size:18px;color:var(--ink)}
.welcome-title{left:581px;top:476px;font-family:'Montserrat',sans-serif;font-weight:600;font-size:33px;color:var(--ink)}
.rule{position:absolute;height:2px;background:var(--ink)}
.welcome-copy{left:582px;top:560px;width:490px;font-size:14.3px;line-height:21px;color:#222}

/* benefits */
.benefits-frame{position:absolute;left:130px;top:1542px;width:758px;height:549px;border:2px solid var(--frame)}
.section-title{position:absolute;font-family:'Montserrat',sans-serif;font-weight:700;font-size:25px;color:var(--ink)}
.benefit{position:absolute;left:163px;display:flex;align-items:center;gap:21px;width:490px}
.benefit svg{flex:0 0 53px;height:60px}
.benefit p{font-size:14.3px;line-height:21px;color:#222}
.photo{position:absolute}

/* why me */
.why{position:absolute;left:0;top:2091px;width:1200px;height:564px;background:linear-gradient(180deg,#ffffff 0%,#f4f2ea 30%,#e4e2c6 60%,#a9b36a 85%,#6d7d36 100%)}
.why-photo{position:absolute;left:760px;top:30px;width:440px;height:534px;background:linear-gradient(160deg,rgba(210,200,170,.5),rgba(120,100,70,.55))}
.why-copy{position:absolute;left:131px;width:480px;font-size:14.3px;line-height:21px;color:#222}

/* footer */
.footer{position:absolute;left:0;top:2655px;width:1200px;height:338px;background:var(--footer);color:var(--white)}
.footer-brand{left:158px;top:148px;font-size:28px;color:var(--white)}
.footer-brand .brand-mark{background:var(--white)}
.col-title{position:absolute;top:47px;font-family:'Montserrat',sans-serif;font-weight:700;font-size:13px}
.menu{position:absolute;left:457px;top:82px;list-style:none;font-family:'Montserrat',sans-serif;font-size:11px;line-height:20px}
.contact{position:absolute;display:flex;align-items:center;gap:10px;font-family:'Montserrat',sans-serif;font-size:11px;line-height:15px}
.icon-dot{width:22px;height:22px;border-radius:50%;background:var(--white);flex:0 0 22px;display:flex;align-items:center;justify-content:center}
.footer-rule{position:absolute;left:137px;top:257px;width:932px;height:1px;background:#3a393d}
.copyright{position:absolute;left:0;width:1200px;top:290px;text-align:center;font-family:'Montserrat',sans-serif;font-size:11px}
</style>
</head>
<body>

<section class="hero">
  <div class="hero-photo" role="img" aria-label="Woman in a light dress with arms outstretched in a sunlit golden meadow"></div>
  <div class="brand header-brand"><span class="brand-mark"></span>CALM SUMMIT</div>
  <nav class="nav">
    <a class="active" style="left:455px">HOME</a>
    <a style="left:539px">ABOUT US</a>
    <a style="left:646px">TRAINING</a>
    <a style="left:748px">SUCCESS TORIES</a>
    <a style="left:903px">BLOG</a>
    <a style="left:971px">CONTACT</a>
  </nav>
  <div class="consult">Schedule<br>Free <svg class="arrow" viewBox="0 0 30 10" style="width:32px;margin-left:8px"><path d="M0 5H28M23 1L28 5L23 9" stroke="#fff" stroke-width="1.4" fill="none"/></svg><br>Consult</div>
  <h1 class="abs hero-title">HEAD COACH</h1>
  <p class="abs hero-copy">Not your typical “quiet whale music playing in the background, kind of “stress guy”….stress is good, it can save your life…</p>
  <a class="btn" style="left:714px;top:402px;width:126px;height:43px">Read More <svg class="arrow" viewBox="0 0 24 10"><path d="M0 5H22M18 1L22 5L18 9" stroke="#fff" stroke-width="1.3" fill="none"/></svg></a>
  <div class="dots"><span></span><span></span><span class="on"></span><span></span><span></span></div>
</section>

<section class="audience">
  <div class="hex" style="left:156px;top:39px">
    <div class="hex-photo" role="img" aria-label="Businessman in a suit celebrating in a city street" style="background:linear-gradient(170deg,#c9cdd3,#7d8794 60%,#3a4150)"></div>
    <div class="hex-band">MEN <svg class="arrow" viewBox="0 0 24 10"><path d="M0 5H22M18 1L22 5L18 9" stroke="#1f1e21" stroke-width="1.3" fill="none"/></svg></div>
    <div class="hex-base" style="background:#2f3442"></div>
  </div>
  <div class="hex" style="left:468px;top:39px">
    <div class="hex-photo" role="img" aria-label="Woman jumping joyfully against a sunset sky" style="background:linear-gradient(180deg,#f3c27a,#e2924a 55%,#8a5a38)"></div>
    <div class="hex-band">WOMEN <svg class="arrow" viewBox="0 0 24 10"><path d="M0 5H22M18 1L22 5L18 9" stroke="#1f1e21" stroke-width="1.3" fill="none"/></svg></div>
    <div class="hex-base" style="background:#5b3a24"></div>
  </div>
  <div class="hex" style="left:778px;top:39px">
    <div class="hex-photo" role="img" aria-label="Two runners silhouetted against the rising sun" style="background:radial-gradient(circle at 50% 55%,#fff2c8,#e9b56a 35%,#8f7a6a 75%)"></div>
    <div class="hex-band">ATHLETES <svg class="arrow" viewBox="0 0 24 10"><path d="M0 5H22M18 1L22 5L18 9" stroke="#1f1e21" stroke-width="1.3" fill="none"/></svg></div>
    <div class="hex-base" style="background:#26221f"></div>
  </div>

  <div class="abs welcome-photo" role="img" aria-label="Woman in a striped top raising her arms in celebration"></div>
  <p class="abs eyebrow">WELCOME TO</p>
  <h2 class="abs welcome-title">CALMSUMMIT</h2>
  <div class="rule" style="left:581px;top:528px;width:245px"></div>
  <p class="abs welcome-copy">Calm Summit came about due to my desire to help people lead a better and healthier life. Initially, I was involved in the fitness/body side of health. As years passed and my experience grew, I realized how important the mind was in total wellness, and that the mind is all powerful and controlling. Control the mind, control the body and achieve success. Stress can be the most debilating factor in our lives, it is the root cause of so many diseases and costs the US workplace an estimated 300 billion dollars due to loss of productivity.</p>
  <a class="btn" style="left:587px;top:733px;width:125px;height:43px">Read More <svg class="arrow" viewBox="0 0 24 10"><path d="M0 5H22M18 1L22 5L18 9" stroke="#fff" stroke-width="1.3" fill="none"/></svg></a>
</section>

<section>
  <div class="benefits-frame"></div>
  <h2 class="section-title" style="left:163px;top:1570px">BENEFITS</h2>
  <div class="rule" style="left:165px;top:1610px;width:49px"></div>

  <div class="benefit" style="top:1642px"><svg viewBox="0 0 52 60"><polygon points="26,0 52,15 52,45 26,60 0,45 0,15" fill="#3a3a3d"/><path d="M16 24H36M16 30H36M16 36H36" stroke="#fff" stroke-width="3"/></svg><p>Experience</p></div>
  <div class="benefit" style="top:1724px"><svg viewBox="0 0 52 60"><polygon points="26,0 52,15 52,45 26,60 0,45 0,15" fill="#3a3a3d"/><circle cx="26" cy="30" r="9" fill="none" stroke="#fff" stroke-width="3"/></svg><p>Sector expert Health/Wellness. Presented at numerous industry shows and quoted in national publications (not as a coach, I’m new, but in the health &amp; wellness space)</p></div>
  <div class="benefit" style="top:1808px"><svg viewBox="0 0 52 60"><polygon points="26,0 52,15 52,45 26,60 0,45 0,15" fill="#3a3a3d"/><path d="M19 24H33M19 30H33M19 36H28" stroke="#fff" stroke-width="3"/></svg><p>Excellent listener…being in sales for many years, the secret is to really listen…and get to the end game, and make it feel as if it was their decision. Not sure how to word this as a benefit.</p></div>
  <div class="benefit" style="top:1895px"><svg viewBox="0 0 52 60"><polygon points="26,0 52,15 52,45 26,60 0,45 0,15" fill="#3a3a3d"/><path d="M17 30L24 37L36 23" stroke="#fff" stroke-width="3" fill="none"/></svg><p>Access/resources industry professionals, sport psychologist…just spent a few hours with the Mind performance coach for the Harbor City Mariners baseball team…I can get the best advice and latest techniques in mind/body training performance.</p></div>
  <div class="benefit" style="top:1991px"><svg viewBox="0 0 52 60"><polygon points="26,0 52,15 52,45 26,60 0,45 0,15" fill="#3a3a3d"/><rect x="18" y="20" width="16" height="20" fill="none" stroke="#fff" stroke-width="3"/></svg><p>Private, more than happy to sign confidentiality agreement. Especially for the business man.</p></div>

  <div class="photo" role="img" aria-label="Man relaxing in a chair with hands behind his head beside a city-view window" style="left:718px;top:1595px;width:340px;height:252px;background:linear-gradient(120deg,#d9dde2,#9aa7b5 55%,#3d5a7a)"></div>
  <div class="photo" role="img" aria-label="Smiling bearded man stretching his arm in a gym" style="left:718px;top:1858px;width:132px;height:173px;background:linear-gradient(160deg,#b7b2aa,#6f665e 60%,#2e2b29)"></div>
  <div class="photo" role="img" aria-label="Person meditating in a yoga pose by the sea at sunset" style="left:862px;top:1858px;width:196px;height:173px;background:linear-gradient(180deg,#e9d6c1,#c9a98c 55%,#5a4a46)"></div>
</section>

<section class="why">
  <div class="why-photo" role="img" aria-label="Woman in a knit hat and scarf sitting on a grassy hillside holding a warm drink"></div>
  <h2 class="section-title" style="left:131px;top:167px">WHY ME?</h2>
  <div class="rule" style="left:131px;top:208px;width:133px;height:3px"></div>
  <p class="why-copy" style="top:250px">Been there done that! Have been through a lot, started businesses, selling a business, law suits, marriage, divorce, second marriage, kids, school, sports, fights, robbed, gun in face, traveled the world, successful, two great kids (both Cadets at Ridgeview Academy…duty/honor/country)</p>
  <p class="why-copy" style="top:362px">Limited number of clients…different stage of life, empty nester, have a full career…won’t be a number</p>
</section>

<footer class="footer">
  <div class="brand footer-brand"><span class="brand-mark"></span>CALM SUMMIT</div>
  <h3 class="col-title" style="left:457px">MENU</h3>
  <ul class="menu"><li>HOME</li><li>ABOUT US</li><li>TRAINING</li><li>SUCCESS STORIES</li><li>BLOG</li><li>CONTACT</li></ul>
  <h3 class="col-title" style="left:654px">CONTACT US</h3>
  <div class="contact" style="left:654px;top:84px"><span class="icon-dot"><svg width="10" height="12" viewBox="0 0 10 12"><path d="M5 12C5 12 0 7 0 4.5A5 5 0 0 1 10 4.5C10 7 5 12 5 12Z" fill="#1d1c1f"/><circle cx="5" cy="4.5" r="1.7" fill="#fff"/></svg></span><span>4150 Larkspur Ave Suite 210<br>Fairhaven, FL&nbsp; 32900</span></div>
  <div class="contact" style="left:654px;top:134px"><span class="icon-dot"><svg width="11" height="11" viewBox="0 0 11 11"><path d="M2 0L4 2.5L3 4C4 6 5 7 7 8L8.5 7L11 9L9.5 11C5 10.5 0.5 6 0 1.5Z" fill="#1d1c1f"/></svg></span><span>Call Us<br>555.014.2288</span></div>
  <div class="contact" style="left:654px;top:186px"><span class="icon-dot"><svg width="11" height="8" viewBox="0 0 11 8"><rect width="11" height="8" fill="#1d1c1f"/><path d="M0 0L5.5 4.5L11 0" stroke="#fff" fill="none"/></svg></span><span>E mail Us<br>hello@calmsummit.com</span></div>
  <h3 class="col-title" style="left:966px">FOLLOW US</h3>
  <div class="contact" style="left:966px;top:84px"><span class="icon-dot"></span><span>Like us on<br>FRIENDLINK</span></div>
  <div class="contact" style="left:966px;top:134px"><span class="icon-dot"></span><span>Follow us on<br>CHIRPER</span></div>
  <div class="contact" style="left:966px;top:186px"><span class="icon-dot"></span><span>Follow us on<br>WORKLINE</span></div>
  <div class="footer-rule"></div>
  <p class="copyright">Copyright © 2022 All Rights Reserved</p>
</footer>

</body>
</html>
```